Modern Business Card

Modern professional business card with more than just logo and demographic info. Something memorable.

We are a trendy/modern chiropractic group with an emphasis on neurology, hence the minimalist-type brain logo. We want to convey that modern and technical aspect with professionalism and the elite nature of our practice environment.

```html
<!DOCTYPE html>
<html lang="en">
<head>
<meta charset="utf-8">
<title>Clarity Spine – Business Card</title>
<link href="https://fonts.googleapis.com/css2?family=Quattrocento:wght@400;700&family=Saira+Semi+Condensed:wght@600&display=swap" rel="stylesheet">
<style>
  :root {
    --backdrop: #b4b4b4;
    --brand-blue: #3e63a0;
    --card-white: #f3f3f3;
    --ink: #2e2a2b;
    --ink-soft: #3c3c3c;
    --on-blue: #f4f4f4;
    --on-blue-soft: #dfe5ef;
  }
  * { box-sizing: border-box; margin: 0; padding: 0; }
  html, body {
    width: 1200px; height: 576px; overflow: hidden;
    background: var(--backdrop);
  }
  .canvas { position: relative; width: 1200px; height: 576px; }

  .card {
    position: absolute;
    border-radius: 10px;
    overflow: hidden;
    box-shadow: 2px 3px 6px rgba(0,0,0,0.25);
  }

  /* Front */
  .card-front {
    left: 82px; top: 139px; width: 485px; height: 293px;
    background: var(--brand-blue);
    color: var(--on-blue);
    font-family: "Quattrocento", serif;
    text-align: center;
  }
  .front-wordmark {
    position: absolute; left: 0; right: 0; top: 96px;
    line-height: 1;
  }
  .front-wordmark .line-main { display: block; font-size: 62px; letter-spacing: 1px; }
  .front-wordmark .line-sub { display: block; font-size: 34px; letter-spacing: 8px; margin-top: 6px; }

  /* Back */
  .card-back {
    left: 602px; top: 138px; width: 481px; height: 291px;
    background: var(--card-white);
    font-family: "Quattrocento", serif;
    color: var(--ink);
  }
  .brand-header {
    position: absolute; left: 27px; top: 24px;
    display: flex; align-items: center; gap: 8px;
    font-size: 25px; letter-spacing: 0.5px; line-height: 1;
  }
  .brand-header .brand-square {
    width: 28px; height: 28px; background: var(--brand-blue);
  }
  .info-band {
    position: absolute; left: 0; right: 0; top: 88px; height: 151px;
    background: var(--brand-blue);
    color: var(--on-blue);
    padding: 17px 27px 0;
  }
  .person-name {
    font-family: "Saira Semi Condensed", sans-serif;
    font-weight: 600; font-size: 19px; line-height: 1.1;
  }
  .person-role { font-size: 12.5px; color: var(--on-blue-soft); margin-top: 4px; }
  .contact-list { list-style: none; margin-top: 19px; }
  .contact-list li {
    display: flex; align-items: center; gap: 10px;
    font-size: 12.5px; height: 18.5px; color: var(--on-blue-soft);
  }
  .contact-list svg { width: 11px; height: 11px; fill: var(--on-blue); flex: none; }
  .postal-address {
    position: absolute; left: 27px; top: 257px;
    font-size: 12.5px; color: var(--ink-soft);
  }
</style>
</head>
<body>
<main class="canvas">
  <section class="card card-front" aria-label="Card front">
    <h1 class="front-wordmark">
      <span class="line-main">CLARITY</span>
      <span class="line-sub">SPINE</span>
    </h1>
  </section>

  <section class="card card-back" aria-label="Card back">
    <div class="brand-header">
      <span class="brand-square"></span>
      <span class="brand-name">CLARITY SPINE</span>
    </div>

    <div class="info-band">
      <p class="person-name">Mara Ellison</p>
      <p class="person-role">Managing Director</p>
      <ul class="contact-list">
        <li>
          <svg viewBox="0 0 12 12" aria-hidden="true"><path d="M1 4.5C1 2.5 3 1.5 6 1.5s5 1 5 3H8.5V3.5h-5v1H1zM2.5 6l2-1.5h3L9.5 6v4.5h-7z"/></svg>
          555-014-2020
        </li>
        <li>
          <svg viewBox="0 0 12 12" aria-hidden="true"><path d="M0.5 2.5h11v7h-11zM1.5 3.2v.5L6 6.8l4.5-3.1v-.5zM1.5 4.9v3.9h9V4.9L6 8z"/></svg>
          mara@clarityspine.com
        </li>
        <li>
          <svg viewBox="0 0 12 12" aria-hidden="true"><path d="M6 .5a5.5 5.5 0 1 0 0 11A5.5 5.5 0 0 0 6 .5zM6 1.6c.6.5 1.1 1.6 1.3 3.1H4.7C4.9 3.2 5.4 2.1 6 1.6zM1.7 6.8h2c.1 1.3.4 2.3.8 3.1A4.4 4.4 0 0 1 1.7 6.8zM1.7 5.2a4.4 4.4 0 0 1 2.8-3.1c-.4.8-.7 1.8-.8 3.1zM6 10.4c-.6-.5-1.1-1.6-1.3-3.6h2.6c-.2 2-.7 3.1-1.3 3.6zM7.5 9.9c.4-.8.7-1.8.8-3.1h2A4.4 4.4 0 0 1 7.5 9.9zM8.3 5.2c-.1-1.3-.4-2.3-.8-3.1a4.4 4.4 0 0 1 2.8 3.1z"/></svg>
          www.clarityspine.com
        </li>
      </ul>
    </div>

    <p class="postal-address">87 Harbor Lane, Westfield, Lakeview, US 204518</p>
  </section>
</main>
</body>
</html>
```